Harborline Renewal Business Card Design

Professional and clean design. The design colors should flow with the logo. Two-sided card with the website on the back which is:

www.HarborlineRenewal.example.

"Specializing in Water Damage Restoration"

On the front I need the name, email, phone, and logo.

Name: Darnell Quisby
Email: Darnell@HarborlineRenewal.example
Phone: 555-318-2046 for now

I only have the Preview and Thumbnail right now but should have the source files uploaded within a day or two.

Target Market(s)

Flood victims, home owners with water damage from busted pipes etc...

Industry/Entity Type

Business

Contact Information for Business Card

Name: Darnell Quisby

Font styles to use
Serif
Sans Serif

Requirements
Must have
• Business Card Details Info

```html
<!DOCTYPE html>
<html lang="en">
<head>
<meta charset="utf-8">
<title>Harborline Renewal Business Card</title>
<link rel="stylesheet" href="https://fonts.googleapis.com/css2?family=Cinzel:wght@400;600;700&family=Open+Sans:wght@400;600&display=swap">
<style>
  :root {
    --page-bg: #e9ecef;
    --brand-blue: #2b96d2;
    --panel-blue: #55bdec;
    --divider-blue: #1f7fc0;
    --ink-dark: #1d2a33;
    --paper-white: #ffffff;
    --card-shadow: rgba(20, 40, 60, 0.18);
  }
  * { box-sizing: border-box; margin: 0; padding: 0; }
  html, body {
    width: 1200px;
    height: 1120px;
    overflow: hidden;
    background: var(--page-bg);
  }
  .canvas {
    width: 1200px;
    height: 1120px;
    display: flex;
    flex-direction: column;
    align-items: center;
    justify-content: center;
    gap: 40px;
  }
  .card {
    width: 940px;
    height: 500px;
    box-shadow: 0 10px 30px var(--card-shadow);
    position: relative;
    overflow: hidden;
  }

  /* Back side */
  .card-back {
    background: var(--brand-blue);
    display: flex;
    flex-direction: column;
    align-items: center;
    color: var(--paper-white);
  }
  .back-mark {
    margin-top: 70px;
    width: 220px;
    height: 220px;
    border-radius: 50%;
    background: var(--paper-white);
  }
  .back-name {
    margin-top: 30px;
    font-family: "Cinzel", serif;
    font-weight: 600;
    font-size: 40px;
    letter-spacing: 2px;
    color: var(--paper-white);
  }
  .tagline {
    margin-top: 18px;
    font-family: "Cinzel", serif;
    font-weight: 400;
    font-size: 27px;
    letter-spacing: 1px;
    color: var(--paper-white);
  }

  /* Front side */
  .card-front {
    display: flex;
    background: var(--paper-white);
  }
  .brand-side {
    width: 430px;
    display: flex;
    flex-direction: column;
    align-items: center;
    justify-content: center;
    gap: 22px;
  }
  .brand-mark {
    width: 110px;
    height: 110px;
    border-radius: 50%;
    background: var(--brand-blue);
  }
  .brand-name {
    font-family: "Cinzel", serif;
    font-weight: 700;
    font-size: 44px;
    line-height: 1.1;
    text-align: center;
    color: var(--brand-blue);
  }
  .divider {
    width: 8px;
    background: var(--divider-blue);
    border-right: 4px solid var(--paper-white);
  }
  .contact-side {
    flex: 1;
    background: var(--panel-blue);
    padding: 100px 0 0 46px;
    color: var(--ink-dark);
  }
  .person-name {
    font-family: "Cinzel", serif;
    font-weight: 700;
    font-size: 34px;
    letter-spacing: 1px;
  }
  .person-title {
    font-family: "Cinzel", serif;
    font-weight: 400;
    font-size: 26px;
    letter-spacing: 3px;
    margin-top: 4px;
  }
  .contact-list {
    list-style: none;
    margin-top: 38px;
    font-family: "Open Sans", sans-serif;
    font-size: 21px;
  }
  .contact-item {
    display: flex;
    align-items: center;
    gap: 12px;
    margin-bottom: 10px;
  }
  .contact-icon {
    width: 20px;
    height: 20px;
    flex: none;
  }
</style>
</head>
<body>
<main class="canvas">
  <section class="card card-back" aria-label="Card back">
    <div class="back-mark"></div>
    <p class="back-name">Harborline Renewal</p>
    <p class="tagline">Specializing in Water Damage Restoration</p>
  </section>

  <section class="card card-front" aria-label="Card front">
    <div class="brand-side">
      <div class="brand-mark"></div>
      <p class="brand-name">Harborline<br>Renewal</p>
    </div>
    <div class="divider"></div>
    <div class="contact-side">
      <h1 class="person-name">Darnell Quisby</h1>
      <p class="person-title">Title</p>
      <ul class="contact-list">
        <li class="contact-item">
          <svg class="contact-icon" viewBox="0 0 20 20" aria-hidden="true">
            <circle cx="10" cy="10" r="9" fill="none" stroke="#1d2a33" stroke-width="1.6"/>
            <path d="M7 5.5l1.6 2.4-1 1.2a6 6 0 0 0 3.3 3.3l1.2-1 2.4 1.6-1 1.6c-3.8 0-7.8-4-7.8-7.8z" fill="#1d2a33"/>
          </svg>
          <span>555-318-2046</span>
        </li>
        <li class="contact-item">
          <svg class="contact-icon" viewBox="0 0 20 20" aria-hidden="true">
            <rect x="2" y="5" width="16" height="11" rx="1.5" fill="#1d2a33"/>
            <path d="M2.5 6l7.5 5 7.5-5" fill="none" stroke="#55bdec" stroke-width="1.4"/>
          </svg>
          <span>Darnell@HarborlineRenewal.example</span>
        </li>
        <li class="contact-item">
          <svg class="contact-icon" viewBox="0 0 20 20" aria-hidden="true">
            <circle cx="10" cy="10" r="8.5" fill="#1d2a33"/>
            <path d="M1.5 10h17M10 1.5c-3 3-3 14 0 17M10 1.5c3 3 3 14 0 17" fill="none" stroke="#55bdec" stroke-width="1.2"/>
          </svg>
          <span>www.HarborlineRenewal.example</span>
        </li>
      </ul>
    </div>
  </section>
</main>
</body>
</html>
```